Business Card Design

We service, sell & install vehicle hoists in automotive workshops & would like the colours royal blue or green incorporated into the design.

Industry/Entity Type

Automotive

Contact Information for Business Card

KLT Lifts
Equipment Sales & Service
Colin Dwyer 0412 558 913
Grant Oakes 0418 762 305
14 Tarn Crescent Wyndale Vic 3521
email: kltlifts@mailbox-example.com.au

```html
<!DOCTYPE html>
<html lang="en">
<head>
<meta charset="utf-8">
<title>KLT Lifts – Business Card</title>
<link rel="stylesheet" href="https://fonts.googleapis.com/css2?family=Open+Sans:wght@300;400;700&family=Oswald:wght@400&display=swap">
<style>
  :root {
    --backdrop: #232323;
    --card: #fafaf9;
    --ink: #262626;
    --ink-soft: #363636;
    --accent: #1f4fc4;
    --decor: #e7edf9;
  }
  * { box-sizing: border-box; margin: 0; padding: 0; }
  html, body {
    width: 1200px; height: 938px; overflow: hidden;
    background: var(--backdrop);
  }
  .card {
    position: absolute; left: 255px; top: 253px;
    width: 692px; height: 431px;
    background: var(--card);
    font-family: "Open Sans", Arial, sans-serif;
    color: var(--ink);
    overflow: hidden;
  }
  .card__decor {
    position: absolute; left: 520px; top: 0;
    width: 172px; height: 431px;
    background: linear-gradient(180deg, var(--card) 0%, var(--decor) 30%, var(--decor) 100%);
  }
  .brand__mark {
    position: absolute; left: 48px; top: 42px;
    width: 78px; height: 78px; border-radius: 50%;
    background: var(--accent);
  }
  .brand__name {
    position: absolute; left: 242px; top: 40px;
    font-family: "Oswald", "Arial Narrow", sans-serif;
    font-weight: 400; font-size: 40px; line-height: 1.1;
    color: var(--ink); text-transform: uppercase; letter-spacing: 0.3px;
  }
  .brand__tagline {
    position: absolute; left: 242px; top: 88px;
    font-weight: 300; font-size: 23px; line-height: 1.2;
    color: var(--ink-soft);
  }
  .person {
    position: absolute; left: 47px; top: 228px;
    font-size: 32px; font-weight: 300; letter-spacing: 0.6px;
    color: var(--ink);
  }
  .person strong { font-weight: 700; }
  .contact {
    position: absolute; right: 46px; top: 302px;
    list-style: none; text-align: right;
  }
  .contact__item {
    display: flex; justify-content: flex-end; align-items: center;
    gap: 12px; height: 30px;
    font-size: 20px; font-weight: 400; color: var(--ink-soft);
  }
  .contact__icon { width: 14px; height: 16px; flex: none; }
</style>
</head>
<body>
  <section class="card">
    <div class="card__decor" role="img" aria-label="Faint illustration of a vehicle hoist"></div>

    <span class="brand__mark"></span>
    <p class="brand__name">KLT Lifts</p>
    <p class="brand__tagline">Equipment Sales &amp; Service</p>

    <p class="person">GRANT <strong>OAKES</strong></p>

    <ul class="contact">
      <li class="contact__item">0418 762 305
        <svg class="contact__icon" viewBox="0 0 14 16" aria-hidden="true">
          <rect x="3" y="1" width="8" height="14" rx="1.5" fill="none" stroke="var(--accent)" stroke-width="1.6"/>
          <rect x="5.5" y="12" width="3" height="1.2" fill="var(--accent)"/>
        </svg>
      </li>
      <li class="contact__item">Tarn Crescent Wyndale Vic 3521
        <svg class="contact__icon" viewBox="0 0 14 16" aria-hidden="true">
          <path d="M7 15 C3 10 2 8 2 6 a5 5 0 0 1 10 0 c0 2 -1 4 -5 9z" fill="var(--accent)"/>
          <circle cx="7" cy="6" r="1.8" fill="var(--card)"/>
        </svg>
      </li>
      <li class="contact__item">kltlifts@mailbox-example.com.au
        <svg class="contact__icon" viewBox="0 0 14 16" aria-hidden="true">
          <rect x="1" y="4.5" width="12" height="8" fill="var(--accent)"/>
          <path d="M1 4.5 L7 9 L13 4.5" fill="none" stroke="var(--card)" stroke-width="1.1"/>
        </svg>
      </li>
    </ul>
  </section>
</body>
</html>
```